Tune Tally Application

Hello,

I want a new design for my Blind test (Tune Tally) application on Korvex. You will find attached the images I want to replace. I need something with the same element (menu / song title) but with a different look!

Same, new icon, you have carte blanche to this one.

I am looking for something fresh…. I'm looking for something with a real artistic choice, contrast, colours, etc.

As a marketing screenshot, I want something classic, you'll find an example attached, feel free to innovate.

To sum-up :

- One new view for my App
- One new icon
- One marketing screenshot

screen resolution :
640×960
icon resolution :
1024x1024

Target Market(s)

15-30 years

Industry/Entity Type

Marketing

```html
<!DOCTYPE html>
<html lang="en">
<head>
<meta charset="utf-8">
<title>Tune Tally – Rankings</title>
<link rel="stylesheet" href="https://fonts.googleapis.com/css2?family=Arimo:wght@400;700&display=swap">
<style>
  :root {
    --status-bg: #0b0b0b;
    --status-text: #ffffff;
    --header-a: #4fb3ad;
    --header-b: #7fcfc4;
    --header-c: #a6dcc8;
    --title: #17324a;
    --tab-home: #6cc5c0;
    --tab-rankings: #cad7cd;
    --tab-community: #a2dcc3;
    --tab-text: #1d3242;
    --sub-general: #cbd3c9;
    --sub-category: #b6beb5;
    --sub-team: #a5ada4;
    --list-bg: #b8c2b7;
    --row-bg: #c9d2c7;
    --row-edge: #dbe2d8;
    --avatar-bg: #e2e8df;
    --ink: #111111;
    --scroll: #e3e8e1;
    --button: #1d3a4f;
  }
  * { box-sizing: border-box; margin: 0; padding: 0; }
  html, body { width: 800px; height: 1200px; overflow: hidden; }
  body { font-family: "Arimo", Arial, sans-serif; background: var(--list-bg); position: relative; }

  .status-bar {
    position: absolute; left: 0; top: 0; width: 800px; height: 45px;
    background: var(--status-bg); color: var(--status-text);
    font-size: 27px; font-weight: 700;
  }
  .status-bar .carrier { position: absolute; left: 14px; top: 7px; display: flex; align-items: center; gap: 8px; }
  .status-bar .time { position: absolute; left: 0; right: 0; top: 7px; text-align: center; }
  .status-bar .battery { position: absolute; right: 14px; top: 10px; }

  .app-header {
    position: absolute; left: 0; top: 45px; width: 800px; height: 112px;
    background: linear-gradient(100deg, var(--header-a) 0%, var(--header-b) 40%, var(--header-c) 70%, var(--header-a) 100%);
  }
  .app-title {
    position: absolute; left: 0; right: 0; top: 28px; text-align: center;
    font-size: 58px; line-height: 64px; font-weight: 700; color: var(--title);
  }
  .round-button { position: absolute; top: 20px; width: 70px; height: 70px; }
  .round-button.menu { left: 5px; }
  .round-button.settings { right: 5px; }

  .main-tabs { position: absolute; left: 0; top: 157px; width: 800px; height: 110px; display: flex; }
  .main-tab {
    flex: 1; display: flex; align-items: center; justify-content: center;
    font-size: 30px; color: var(--tab-text); border-right: 2px solid rgba(255,255,255,0.5);
  }
  .main-tab.home { background: var(--tab-home); }
  .main-tab.rankings { background: var(--tab-rankings); }
  .main-tab.community { background: var(--tab-community); border-right: 0; }

  .sub-tabs { position: absolute; left: 0; top: 277px; width: 800px; height: 70px; display: flex; }
  .sub-tab { display: flex; align-items: center; justify-content: center; font-size: 29px; color: var(--ink); }
  .sub-tab.general { width: 267px; background: var(--sub-general); }
  .sub-tab.category { width: 277px; background: var(--sub-category); }
  .sub-tab.team { width: 256px; background: var(--sub-team); }

  .ranking-list { position: absolute; left: 0; top: 347px; width: 800px; height: 853px; background: var(--list-bg); overflow: hidden; }
  .ranking-row {
    position: absolute; left: 21px; width: 758px; height: 142px;
    background: var(--row-bg); border: 3px solid var(--row-edge);
  }
  .rank { position: absolute; left: 52px; top: 38px; font-size: 56px; color: var(--ink); }
  .avatar { position: absolute; left: 150px; top: 21px; width: 94px; height: 94px; background: var(--avatar-bg); }
  .account-name { position: absolute; left: 264px; top: 30px; font-size: 38px; color: var(--ink); }
  .points { position: absolute; left: 264px; top: 74px; font-size: 19px; color: var(--ink); }

  .scroll-thumb { position: absolute; right: 2px; top: 547px; width: 10px; height: 253px; background: var(--scroll); }
</style>
</head>
<body>
  <div class="status-bar">
    <div class="carrier">
      <svg width="30" height="24" viewBox="0 0 30 24" aria-hidden="true">
        <rect x="0" y="16" width="4" height="8" fill="#fff"/>
        <rect x="6" y="12" width="4" height="12" fill="#fff"/>
        <rect x="12" y="8" width="4" height="16" fill="#fff"/>
        <rect x="18" y="4" width="4" height="20" fill="#fff"/>
        <rect x="24" y="0" width="4" height="24" fill="#fff"/>
      </svg>
      <span>NIMBAL</span>
    </div>
    <div class="time">2:34</div>
    <svg class="battery" width="58" height="26" viewBox="0 0 58 26" aria-hidden="true">
      <rect x="1.5" y="1.5" width="50" height="23" rx="3" fill="none" stroke="#fff" stroke-width="3"/>
      <rect x="6" y="6" width="41" height="14" fill="#fff"/>
      <rect x="53" y="8" width="4" height="10" fill="#fff"/>
    </svg>
  </div>

  <header class="app-header">
    <svg class="round-button menu" viewBox="0 0 70 70" aria-label="Menu">
      <circle cx="35" cy="35" r="32" fill="#1d3a4f"/>
      <circle cx="35" cy="35" r="28" fill="none" stroke="#fff" stroke-width="2"/>
      <g fill="#fff">
        <rect x="20" y="23" width="5" height="5"/><rect x="29" y="23" width="21" height="5"/>
        <rect x="20" y="33" width="5" height="5"/><rect x="29" y="33" width="21" height="5"/>
        <rect x="20" y="43" width="5" height="5"/><rect x="29" y="43" width="21" height="5"/>
      </g>
    </svg>
    <h1 class="app-title">Tune Tally</h1>
    <svg class="round-button settings" viewBox="0 0 70 70" aria-label="Settings">
      <circle cx="35" cy="35" r="32" fill="#1d3a4f"/>
      <circle cx="35" cy="35" r="28" fill="none" stroke="#fff" stroke-width="2"/>
      <g fill="#fff" transform="translate(35 35)">
        <rect x="-4" y="-18" width="8" height="36"/>
        <rect x="-4" y="-18" width="8" height="36" transform="rotate(45)"/>
        <rect x="-4" y="-18" width="8" height="36" transform="rotate(90)"/>
        <rect x="-4" y="-18" width="8" height="36" transform="rotate(135)"/>
        <circle r="13"/>
      </g>
      <circle cx="35" cy="35" r="6" fill="#1d3a4f"/>
    </svg>
  </header>

  <nav class="main-tabs">
    <div class="main-tab home">HOME</div>
    <div class="main-tab rankings">RANKINGS</div>
    <div class="main-tab community">COMMUNITY</div>
  </nav>

  <nav class="sub-tabs">
    <div class="sub-tab general">GENERAL</div>
    <div class="sub-tab category">BY CATEGORY</div>
    <div class="sub-tab team">BY TEAM</div>
  </nav>

  <svg width="0" height="0" style="position:absolute">
    <defs>
      <g id="avatar-icon">
        <rect x="30" y="16" width="42" height="42" rx="4" fill="#111"/>
        <rect x="24" y="22" width="42" height="42" rx="4" fill="#111" stroke="#e2e8df" stroke-width="3"/>
        <rect x="18" y="28" width="42" height="42" rx="4" fill="#111" stroke="#e2e8df" stroke-width="3"/>
        <rect x="24" y="34" width="30" height="30" fill="#e2e8df"/>
        <circle cx="39" cy="45" r="6" fill="#111"/>
        <path d="M28 64 Q39 50 50 64 Z" fill="#111"/>
      </g>
    </defs>
  </svg>

  <main class="ranking-list">
    <div class="ranking-row" style="top:16px"><span class="rank">1.</span><svg class="avatar" viewBox="0 0 94 94" aria-hidden="true"><use href="#avatar-icon"/></svg><span class="account-name">ACCOUNT NAME</span><span class="points">39 Points</span></div>
    <div class="ranking-row" style="top:168px"><span class="rank">2.</span><svg class="avatar" viewBox="0 0 94 94" aria-hidden="true"><use href="#avatar-icon"/></svg><span class="account-name">ACCOUNT NAME</span><span class="points">39 Points</span></div>
    <div class="ranking-row" style="top:320px"><span class="rank">3.</span><svg class="avatar" viewBox="0 0 94 94" aria-hidden="true"><use href="#avatar-icon"/></svg><span class="account-name">ACCOUNT NAME</span><span class="points">39 Points</span></div>
    <div class="ranking-row" style="top:472px"><span class="rank">4.</span><svg class="avatar" viewBox="0 0 94 94" aria-hidden="true"><use href="#avatar-icon"/></svg><span class="account-name">ACCOUNT NAME</span><span class="points">39 Points</span></div>
    <div class="ranking-row" style="top:624px"><span class="rank">5.</span><svg class="avatar" viewBox="0 0 94 94" aria-hidden="true"><use href="#avatar-icon"/></svg><span class="account-name">ACCOUNT NAME</span><span class="points">39 Points</span></div>
    <div class="ranking-row" style="top:776px"><span class="rank">6.</span><svg class="avatar" viewBox="0 0 94 94" aria-hidden="true"><use href="#avatar-icon"/></svg><span class="account-name">ACCOUNT NAME</span><span class="points">39 Points</span></div>
  </main>

  <div class="scroll-thumb"></div>
</body>
</html>
```